Enrollment Campaign

We need a flyer design for our school's enrollment campaign. Our school website is www.tbvacademy.net.

The flyer should be double sided.

I want the reader to get the following messages:
1. Montessori graduates are leading the top companies of our time.
2. We are an accredited Montessori school.
3. Enrollment is open now for all four programs:
a) Toddler: 18months (or as soon as the child is able to walk) - 3 years
b) CASA: Preschool to Senior Kindergarten (3 years to 6 years)
c) Elementary: Grades 1 to 6
d) Junior High: Grades 7 to 8
4) Our contact information:
website, email:info@tbvacademy.net, phone: 647 382 5146
5) Call for Action: Book a Tour! (there is a button on our website to book a tour)
6) In the languages punjabi, hindi and italian, I wouldn't readers to know that we offer their faith and cultural education as well.
7) Fees for children under age of 6 can be claimed in Taxes as day care expense. So, there is no reason to miss providing our children the best that we can in education.
Updates

Please note my updates to my brief in the "must have" section. Also, I have added some pics that can be used. Please note that I don't have one pic (the farming one referred to in my brief). I will really appreciate if you can kindly update your design accordingly.

Reason: Because of my recent update to the brief, some designers need some time to adjust their designs. I really appreciate your patience and kind consideration for my project. Thank you!

Industry/Entity Type

Education

Colors

Designer to choose colors to be used in the design.

Requirements
Must have
• Must have a unique design. I don't want a typical flyer. The design should be unique and memorable.

One of the main pics that I need is for illustrating a key feature of our new Junior High program that we are starting in August 2015. The key feature is that children are going to be operating a 'greenhouse', growing organic produce and will also be preparing their daily lunch from scratch. So, show a pic of a 13-14year old farming or something.

```html
<!DOCTYPE html>
<html lang="en">
<head>
<meta charset="utf-8">
<title>TBV Academy – Admission Open</title>
<link href="https://fonts.googleapis.com/css2?family=Open+Sans:wght@300;400;700&family=Courgette&display=swap" rel="stylesheet">
<style>
  :root {
    --sky: #55c8f0;
    --lime: #7ed321;
    --lime-pin: #5cc21a;
    --ink: #555659;
    --ink-dark: #3c3c3e;
    --body-grey: #5d5e61;
    --rule-pink: #e58a9b;
    --paper: #ffffff;
  }
  html, body { margin: 0; padding: 0; overflow: hidden; background: var(--paper); }
  .flyer {
    position: relative; width: 934px; height: 1200px; overflow: hidden;
    background: var(--paper); font-family: "Open Sans", sans-serif; color: var(--ink);
  }
  .abs { position: absolute; }

  .brand {
    left: 90px; top: 46px; margin: 0; width: 170px;
    font-family: "Open Sans", sans-serif; font-weight: 700; font-size: 32px;
    line-height: 36px; color: var(--sky); letter-spacing: -1px;
  }
  .headline {
    left: 284px; top: 48px; margin: 0; font-size: 38px; font-weight: 700;
    color: var(--ink); letter-spacing: -1.2px; white-space: nowrap; line-height: 50px;
  }
  .headline .accent {
    font-family: "Courgette", cursive; font-weight: 400; font-size: 20px;
    color: var(--ink); margin-left: 10px; letter-spacing: 0;
  }
  .tagline {
    left: 250px; top: 112px; margin: 0; font-family: "Courgette", cursive;
    font-size: 37px; line-height: 50px; color: var(--lime); white-space: nowrap;
  }
  .claim {
    left: 240px; top: 170px; width: 500px; margin: 0; text-align: center;
    font-size: 24px; font-weight: 700; line-height: 30px; color: var(--ink); letter-spacing: -0.8px;
  }

  .rule { left: 38px; width: 834px; height: 6px; border-top: 1.5px solid var(--rule-pink); border-bottom: 1.5px solid var(--rule-pink); }

  .strings { left: 0; top: 0; }
  .admission {
    left: 140px; top: 284px; width: 340px; height: 180px; background: var(--sky);
    border-radius: 14px; transform: rotate(4deg); box-shadow: 2px 4px 6px rgba(0,0,0,.12);
  }
  .admission::after {
    content: ""; position: absolute; inset: 10px; border: 2px solid rgba(255,255,255,.85); border-radius: 8px;
  }
  .admission .word { position: absolute; left: 0; right: 0; text-align: center; color: var(--paper); margin: 0; }
  .admission .word-main { top: 28px; font-size: 46px; font-weight: 700; letter-spacing: -1px; }
  .admission .word-script { top: 86px; font-family: "Courgette", cursive; font-size: 46px; }

  .pin {
    width: 16px; height: 16px; border-radius: 50%;
    background: radial-gradient(circle at 35% 35%, #c6f59a, var(--lime-pin) 60%, #3e9a10);
    box-shadow: 1px 2px 3px rgba(0,0,0,.3); z-index: 3;
  }

  .snapshot {
    box-sizing: border-box; background: var(--paper); border: 12px solid var(--lime);
    padding: 8px; box-shadow: 2px 4px 8px rgba(0,0,0,.15);
  }
  .snapshot .fill { width: 100%; height: 100%; }
  .snap-a { left: 536px; top: 262px; width: 226px; height: 214px; transform: rotate(6deg); }
  .snap-a .fill { background: linear-gradient(160deg, #c9a27a, #6e4b33 70%, #3a2a22); }
  .snap-b { left: 618px; top: 456px; width: 214px; height: 208px; transform: rotate(-5deg); }
  .snap-b .fill { background: linear-gradient(150deg, #e8d6d3, #c99a8d 60%, #8a6c5c); }
  .snap-c { left: 514px; top: 620px; width: 232px; height: 220px; transform: rotate(8deg); }
  .snap-c .fill { background: linear-gradient(140deg, #5f8a3e, #3a78b8 60%, #2c3a55); }
  .snap-d { left: 592px; top: 834px; width: 236px; height: 214px; transform: rotate(-5deg); }
  .snap-d .fill { background: linear-gradient(150deg, #d9dcd6, #7d98b4 55%, #3c4a68); }

  .intro { left: 90px; top: 518px; margin: 0; font-size: 22px; font-weight: 300; line-height: 42px; color: var(--ink); letter-spacing: -0.4px; }
  .intro strong { font-weight: 700; }

  .programs { left: 96px; top: 0; width: 400px; margin: 0; padding: 0; list-style: none; }
  .programs li {
    position: absolute; left: 0; width: 400px; box-sizing: border-box; padding-left: 48px;
    font-size: 19.5px; line-height: 22px; color: #2f2f31; font-weight: 400; letter-spacing: -0.2px;
  }
  .programs li::before {
    content: ""; position: absolute; left: 0; top: 6px; width: 16px; height: 16px; border-radius: 50%;
    background: radial-gradient(circle at 35% 35%, #c6f59a, var(--lime-pin) 60%, #3e9a10);
    box-shadow: 1px 3px 4px rgba(0,0,0,.25);
  }
  .programs strong { font-weight: 700; }
  .programs .p-toddler { top: 626px; }
  .programs .p-casa { top: 681px; }
  .programs .p-elem { top: 734px; }
  .programs .p-junior { top: 789px; }
  .programs .p-lang { top: 840px; padding-left: 53px; }

  .tax-note { left: 92px; top: 908px; width: 460px; margin: 0; font-size: 20px; font-weight: 300; line-height: 24px; color: var(--body-grey); white-space: nowrap; }

  .contact { left: 198px; top: 1031px; margin: 0; font-size: 19.5px; line-height: 24px; font-weight: 700; color: var(--ink-dark); }
  .contact span { font-weight: 400; }

  .tour {
    left: 500px; top: 1014px; width: 148px; height: 78px; background: var(--sky);
    border-radius: 10px; transform: rotate(-5deg); text-align: center; color: var(--paper);
    box-shadow: 1px 3px 5px rgba(0,0,0,.15);
  }
  .tour::after { content: ""; position: absolute; inset: 5px; border: 1.5px solid rgba(255,255,255,.85); border-radius: 7px; }
  .tour .cta { margin: 12px 0 0; font-size: 15px; font-weight: 300; }
  .tour .cta em { font-family: "Courgette", cursive; font-style: normal; font-size: 20px; }
  .tour .url { margin: 2px 0 0; font-size: 11.5px; }
</style>
</head>
<body>
<main class="flyer">
  <p class="abs brand">TBV<br>Academy</p>
  <h1 class="abs headline">Free the learning<span class="accent">spirit</span></h1>
  <p class="abs tagline">Faith &amp; and ethnic culture</p>
  <p class="abs claim">Montessori graduates are leading<br>the top companies of our time.</p>

  <div class="abs rule" style="top:283px"></div>
  <div class="abs rule" style="top:441px"></div>
  <div class="abs rule" style="top:1104px;left:60px;width:830px"></div>

  <svg class="abs strings" width="934" height="1200" viewBox="0 0 934 1200" aria-hidden="true">
    <path d="M330 265 L255 292 M330 265 L402 306" stroke="#8a8a8a" stroke-width="1.5" fill="none"/>
    <path d="M590 1000 L548 1016 M590 1000 L632 1010" stroke="#8a8a8a" stroke-width="1.5" fill="none"/>
  </svg>
  <div class="abs admission">
    <p class="word word-main">ADMISSION</p>
    <p class="word word-script">Open</p>
  </div>
  <div class="abs pin" style="left:322px;top:257px"></div>

  <div class="abs snapshot snap-a"><div class="fill" role="img" aria-label="Photo of a young boy in a patka working with a wooden Montessori material"></div></div>
  <div class="abs pin" style="left:578px;top:256px"></div>
  <div class="abs snapshot snap-b"><div class="fill" role="img" aria-label="Photo of a girl threading yarn in a hands-on activity"></div></div>
  <div class="abs pin" style="left:612px;top:475px"></div>
  <div class="abs snapshot snap-c"><div class="fill" role="img" aria-label="Photo of a child looking through binoculars outdoors"></div></div>
  <div class="abs pin" style="left:558px;top:612px"></div>
  <div class="abs snapshot snap-d"><div class="fill" role="img" aria-label="Photo of students working together at a classroom table"></div></div>
  <div class="abs pin" style="left:584px;top:855px"></div>

  <p class="abs intro">ENROLLMENT IS OPEN NOW<br>FOR <strong>ALL FOUR PROGRAMS:</strong></p>

  <ul class="abs programs">
    <li class="p-toddler"><strong>Toddler:</strong> 18months (or as soon as<br>the child is able to walk) - 3 years</li>
    <li class="p-casa"><strong>CASA:</strong> Preschool to Senior Kinder-<br>garten (3 years to 6 years)</li>
    <li class="p-elem"><strong>Elementary:</strong> Grades 1 to 6</li>
    <li class="p-junior"><strong>Junior High:</strong> Grades 7 to 8</li>
    <li class="p-lang">In the languages <strong>punjabi, hindi<br>and italian</strong></li>
  </ul>

  <p class="abs tax-note">Fees for children under age of 6 can be<br>claimed in Taxes as day care expense. So,<br>there is no reason to miss providing our<br>children the best that we can in education.</p>

  <p class="abs contact">Phone: <span>647 382 5146</span><br>Email: <span>info@tbvacademy.net</span><br>Website: <span>www.tbvacademy.net</span></p>

  <div class="abs tour">
    <p class="cta">BOOK A <em>TOUR</em></p>
    <p class="url">www.tbvacademy.net</p>
  </div>
  <div class="abs pin" style="left:582px;top:992px;width:12px;height:12px"></div>
</main>
</body>
</html>
```